Business card por a urban DJ, up scale audience target

Need a sober design, modern, conservative colors but i can consider some options, y play rnb, hip hop, EDM and top40.

Business card for contact and personal info, double sided, use logo attrached please; im 42 so i need a card acording to my age an target audience.

Target Market(s)

Adult people, up scale audience

Industry/Entity Type

Music Download

Contact Information for Business Card

Cel (318) 4207265518 www.lumadrift.com

Requirements
Must have
• open mind
Nice to have
• open mind
Should not have
• DJ

```html
<!DOCTYPE html>
<html lang="en">
<head>
<meta charset="utf-8">
<title>Lumadrift Business Card</title>
<link href="https://fonts.googleapis.com/css2?family=Open+Sans:wght@400;600;700;800&display=swap" rel="stylesheet">
<style>
  :root {
    --ink: #1a1a1a;
    --paper: #ffffff;
    --backdrop: #d6d6d6;
    --text-dark: #222222;
  }
  * { box-sizing: border-box; margin: 0; padding: 0; }
  html, body { width: 1200px; height: 800px; overflow: hidden; }
  body {
    background: var(--backdrop);
    font-family: "Open Sans", Arial, sans-serif;
    position: relative;
  }
  .card {
    position: absolute;
    top: 90px;
    width: 360px;
    height: 620px;
    box-shadow: 0 6px 18px rgba(0,0,0,0.25);
  }
  .card--front { left: 200px; background: var(--paper); }
  .card--back  { left: 640px; background: var(--ink); }

  .card__panel {
    position: absolute;
    left: 24px; top: 24px;
    width: 312px; height: 506px;
  }
  .card--front .card__panel { background: var(--ink); }
  .card--back  .card__panel { background: var(--paper); }

  .card__stripes { position: absolute; left: 0; top: 0; width: 360px; height: 620px; }
  .card--front .card__stripes polygon { fill: var(--paper); }
  .card--back  .card__stripes polygon { fill: var(--ink); }

  .brand-name {
    position: absolute;
    left: 0; right: 0; top: 88px;
    text-align: center;
    font-weight: 800;
    font-size: 92px;
    line-height: 1;
    letter-spacing: 2px;
  }
  .card--front .brand-name { color: var(--paper); }
  .card--back  .brand-name { color: var(--ink); }

  .card__url {
    position: absolute;
    left: 0; right: 0; top: 530px; height: 90px;
    display: flex; align-items: center; justify-content: center;
    font-weight: 700;
    font-size: 21px;
    letter-spacing: 0.3px;
  }
  .card--front .card__url { color: var(--text-dark); }
  .card--back  .card__url { color: var(--paper); }

  .contact {
    position: absolute;
    left: 0; right: 0; top: 310px;
    text-align: center;
    color: var(--text-dark);
  }
  .contact__name { font-weight: 600; font-size: 22px; letter-spacing: 0.5px; }
  .contact__role { font-weight: 400; font-size: 15px; margin-top: 2px; }
  .contact__phone { font-weight: 700; font-size: 19px; margin-top: 46px; letter-spacing: 0.3px; }
</style>
</head>
<body>

  <section class="card card--front">
    <div class="card__panel"></div>
    <svg class="card__stripes" viewBox="0 0 360 620" aria-hidden="true">
      <polygon points="24,110 52,132 52,156 24,134"/>
      <polygon points="24,156 52,178 52,202 24,180"/>
      <polygon points="24,202 52,224 52,248 24,226"/>
      <polygon points="336,110 308,132 308,156 336,134"/>
      <polygon points="336,156 308,178 308,202 336,180"/>
      <polygon points="336,202 308,224 308,248 336,226"/>
    </svg>
    <div class="brand-name">LUMA</div>
    <div class="card__url">www.lumadrift.com</div>
  </section>

  <section class="card card--back">
    <div class="card__panel"></div>
    <svg class="card__stripes" viewBox="0 0 360 620" aria-hidden="true">
      <polygon points="24,110 52,132 52,156 24,134"/>
      <polygon points="24,156 52,178 52,202 24,180"/>
      <polygon points="24,202 52,224 52,248 24,226"/>
      <polygon points="336,110 308,132 308,156 336,134"/>
      <polygon points="336,156 308,178 308,202 336,180"/>
      <polygon points="336,202 308,224 308,248 336,226"/>
    </svg>
    <div class="brand-name">LUMA</div>
    <div class="contact">
      <div class="contact__name">EMPLOYEE NAME</div>
      <div class="contact__role">Director,</div>
      <div class="contact__phone">(318) 4207265518</div>
    </div>
    <div class="card__url">www.lumadrift.com</div>
  </section>

</body>
</html>
```